Quality Monitoring Company Needs a New Site

We are an established company that has a fair number of clients but the site lacks current design standards that we'd like to keep up with. We'd like to mimic the same style of the site on plinkora.com, vetrumo.com, https://brindlecoffer.com/, etc. We'd also like to make sure the designer understands SEO Silos and how it effects the design elements. Attached is the structure that I'd like to follow for the pages. You don't need to design every single sub-page because they'll probably be fairly similar; however, I want to see at least 1 each. Please use the content on our current site for filler areas. Please try to do a good job of understanding what we do so you can use your best judgement on what is needed to be successful. Use our color scheme and the logo should be the side view but I included the AI just in case.
Updates

I am narrowing down on the field of designs that I have received. There are a lot of similarities between the designs I like and don't like. I'd also like to ensure that some of the inner pages get done in the next 5 days so I can see the creativity that is there as well. That is probably what is next -- getting a few inner pages completed so I can see what you can come up with (not based on our current website) because the current "front pages" are all so good and so close.

Industry/Entity Type

Telecommunications

Colors

Designer to choose colors to be used in the design.

Requirements
Must have
• SEO Silo Look and Feel
• Current Colors
Should not have
• No stockphotos whatsoever. NONE.

```html
<!DOCTYPE html>
<html lang="en">
<head>
<meta charset="utf-8">
<title>Coaching | Callvera</title>
<link href="https://fonts.googleapis.com/css2?family=Montserrat:wght@700;800&family=Poppins:wght@400;500;600&display=swap" rel="stylesheet">
<style>
  :root{
    --bg:#f5f6fa;
    --blob:#e9ebf3;
    --navy:#012c57;
    --ink:#0b2a4d;
    --text:#5d6470;
    --cyan:#06b4e6;
    --white:#ffffff;
    --rule:#1e4a75;
  }
  *{margin:0;padding:0;box-sizing:border-box}
  html,body{width:1200px;height:1180px;overflow:hidden;background:var(--bg)}
  body{position:relative;font-family:"Poppins",sans-serif;color:var(--text)}
  .abs{position:absolute}
  .blob{left:0;top:0}
  .brand{left:139px;top:56px;display:flex;align-items:center;gap:8px}
  .brand-dot{width:16px;height:16px;border-radius:50%;background:var(--cyan)}
  .brand-name{font-family:"Poppins",sans-serif;font-weight:500;font-size:22px;color:var(--navy);letter-spacing:.2px}
  .nav{top:77px;left:0;font-size:12.5px;color:#2b3440}
  .nav a{position:absolute;color:inherit;text-decoration:none;white-space:nowrap}
  .nav a.active{color:var(--cyan);font-weight:600}
  .call{left:904px;top:64px;display:flex;align-items:center;gap:8px}
  .call-icon{width:38px;height:38px;border-radius:50%;background:var(--cyan);display:flex;align-items:center;justify-content:center}
  .call-num{font-weight:600;font-size:14px;color:var(--navy);letter-spacing:.4px}
  .dropdown{z-index:5;left:443px;top:102px;width:184px;height:134px;background:var(--white);border-radius:3px;box-shadow:0 6px 18px rgba(20,40,80,.08);font-size:10.2px;color:#555c66;letter-spacing:0}
  .dropdown div{position:absolute;left:17px;white-space:nowrap}
  .dropdown .current{left:7px;width:170px;height:29px;background:var(--cyan);color:var(--white);font-weight:600;padding:7px 0 0 10px;border-radius:2px}
  .page-title{left:139px;top:189px;font-family:"Montserrat",sans-serif;font-weight:800;font-size:30px;color:var(--navy)}
  .title-rule{left:140px;top:239px;width:35px;height:2px;background:var(--cyan)}
  .copy{left:143px;width:460px;font-size:11.2px;line-height:19px;letter-spacing:.15px}
  .ticks{left:142px;top:432px;list-style:none;font-size:11.4px;letter-spacing:.15px}
  .ticks li{display:flex;align-items:center;gap:12px;height:32.5px}
  .art{left:607px;top:187px;width:494px;height:374px;border-radius:8px;background:linear-gradient(135deg,#dfe6f0 0%,#c9e9f6 55%,#e3e7ee 100%)}
  .footer{left:0;top:806px;width:1200px;height:374px;background:var(--navy)}
  .shout{left:211px;top:701px;width:777px;height:211px;border-radius:106px;background:var(--cyan);text-align:center}
  .shout h2{margin-top:48px;font-weight:400;font-size:43px;color:var(--white);letter-spacing:.5px}
  .shout a{display:inline-block;margin-top:16px;width:155px;height:36px;line-height:36px;border-radius:18px;background:var(--navy);color:var(--white);font-size:13.5px;text-decoration:none;letter-spacing:.3px}
  .foot-head{top:967px;font-family:"Montserrat",sans-serif;font-weight:700;font-size:17px;color:var(--cyan)}
  .foot-links{list-style:none;font-size:11.4px;color:var(--white)}
  .foot-links li{height:20.3px}
  .contact{font-size:12.5px;color:var(--white);line-height:23px;display:flex;gap:9px}
  .foot-brand{left:935px;top:998px;display:flex;align-items:center;gap:10px}
  .foot-brand .dot{width:22px;height:22px;border-radius:50%;background:var(--cyan)}
  .foot-brand span{font-weight:500;font-size:26px;color:var(--white)}
  .foot-rule{left:139px;top:1133px;width:919px;height:1px;background:var(--rule)}
  .copyright{left:0;top:1148px;width:1200px;text-align:center;font-size:12.3px;color:var(--white)}
</style>
</head>
<body>
  <svg class="abs blob" width="1200" height="620" viewBox="0 0 1200 620" aria-hidden="true">
    <path d="M860 0 C760 120 650 230 690 380 C730 520 900 610 1200 600 L1200 0 Z" fill="var(--blob)"/>
  </svg>

  <header>
    <div class="abs brand"><span class="brand-dot"></span><span class="brand-name">Callvera</span></div>
    <nav class="abs nav">
      <a style="left:404px">Home</a>
      <a class="active" style="left:463px">Services</a>
      <a style="left:537px">Industries</a>
      <a style="left:620px">Pricing</a>
      <a style="left:683px">Team</a>
      <a style="left:742px">Blog</a>
      <a style="left:793px">Contact Us</a>
    </nav>
    <div class="abs call">
      <span class="call-icon">
        <svg width="15" height="15" viewBox="0 0 24 24"><path fill="#fff" d="M6.6 10.8a15.1 15.1 0 0 0 6.6 6.6l2.2-2.2c.3-.3.7-.4 1-.2 1.1.4 2.3.6 3.6.6.6 0 1 .4 1 1V20c0 .6-.4 1-1 1A17 17 0 0 1 3 4c0-.6.4-1 1-1h3.5c.6 0 1 .4 1 1 0 1.3.2 2.5.6 3.6.1.3 0 .7-.2 1z"/></svg>
      </span>
      <span class="call-num">555-214-7730</span>
    </div>
  </header>

  <main>
    <h1 class="abs page-title">Coaching</h1>
    <span class="abs title-rule"></span>
    <p class="abs copy" style="top:261px">Lorem ipsum dolor sit amet, consectetuer adipiscing elit, sed diam nonummy nibh euismod tincidunt ut laoreet dolore magna aliquam erat volutpat. Ut wisi enim ad minim veniam, quis nostrud exerci tation ullamcorper suscipit lobortis nisl ut aliquip ex ea commodo consequat.</p>
    <p class="abs copy" style="top:356px">Lorem ipsum dolor sit amet, consectetuer adipiscing elit, sed diam nonummy nibh euismod tincidunt ut laoreet dolore magna aliquam erat volutpat. Ut wisi enim ad minim veniam, quis nostrud exerci tation</p>
    <ul class="abs ticks">
      <li><svg width="11" height="9" viewBox="0 0 11 9"><path d="M1 4.5l3 3L10 1" stroke="var(--cyan)" stroke-width="2" fill="none"/></svg>Consectetuer adipiscing elit sed diam nonummy</li>
      <li><svg width="11" height="9" viewBox="0 0 11 9"><path d="M1 4.5l3 3L10 1" stroke="var(--cyan)" stroke-width="2" fill="none"/></svg>Nibh euismod tincidunt ut laoreet dolore magna</li>
      <li><svg width="11" height="9" viewBox="0 0 11 9"><path d="M1 4.5l3 3L10 1" stroke="var(--cyan)" stroke-width="2" fill="none"/></svg>Aliquam erat volutpat. Ut wisi enim ad minim veniam</li>
      <li><svg width="11" height="9" viewBox="0 0 11 9"><path d="M1 4.5l3 3L10 1" stroke="var(--cyan)" stroke-width="2" fill="none"/></svg>Quis nostrud exerci tation ullamcorper suscipit lobortis</li>
    </ul>
    <div class="abs art" role="img" aria-label="Illustration of two coaches presenting performance charts on a large dashboard screen"></div>
  </main>

  <div class="abs dropdown">
    <div style="top:14px">Quality Assurance</div>
    <div class="current" style="top:36px">Coaching</div>
    <div style="top:73px">Sales Performance</div>
    <div style="top:102px">Ai Enabled Voice Analytics</div>
  </div>

  <footer>
    <div class="abs footer"></div>
    <section class="abs shout">
      <h2>Give Us A Shout</h2>
      <a>GET IN TOUCH</a>
    </section>

    <h3 class="abs foot-head" style="left:139px">Quick Links</h3>
    <ul class="abs foot-links" style="left:139px;top:1004px">
      <li>Home</li><li>Services</li><li>System Details</li><li>Pricing</li>
    </ul>
    <ul class="abs foot-links" style="left:294px;top:1004px">
      <li>Team</li><li>Blog</li><li>Contact Us</li><li>Login</li>
    </ul>

    <h3 class="abs foot-head" style="left:460px">Contact Us</h3>
    <div class="abs contact" style="left:462px;top:1002px">
      <svg width="11" height="16" viewBox="0 0 11 16" style="margin-top:5px"><path d="M5.5 0A5.5 5.5 0 0 0 0 5.5C0 9.6 5.5 16 5.5 16S11 9.6 11 5.5A5.5 5.5 0 0 0 5.5 0zm0 7.6a2.1 2.1 0 1 1 0-4.2 2.1 2.1 0 0 1 0 4.2z" fill="#fff"/></svg>
      <span>4810 Meridian Ave.<br>Harbor City, CA 90000</span>
    </div>
    <div class="abs contact" style="left:660px;top:1002px">
      <svg width="14" height="14" viewBox="0 0 24 24" style="margin-top:5px"><path fill="#fff" d="M6.6 10.8a15.1 15.1 0 0 0 6.6 6.6l2.2-2.2c.3-.3.7-.4 1-.2 1.1.4 2.3.6 3.6.6.6 0 1 .4 1 1V20c0 .6-.4 1-1 1A17 17 0 0 1 3 4c0-.6.4-1 1-1h3.5c.6 0 1 .4 1 1 0 1.3.2 2.5.6 3.6.1.3 0 .7-.2 1z"/></svg>
      <span>555-214-7730</span>
    </div>
    <div class="abs contact" style="left:660px;top:1038px">
      <svg width="15" height="11" viewBox="0 0 15 11" style="margin-top:7px"><rect width="15" height="11" rx="1" fill="#fff"/><path d="M1 1l6.5 5L14 1" stroke="var(--navy)" stroke-width="1.3" fill="none"/></svg>
      <span>hello@callvera.com</span>
    </div>

    <div class="abs foot-brand"><span class="dot"></span><span>Callvera</span></div>

    <div class="abs foot-rule"></div>
    <p class="abs copyright">Copyright © 2019 CALLVERA.. All Rights Reserved.</p>
  </footer>
</body>
</html>
```